IT Company requires new Business Card design.

Over the years we have had a few different business card designs. We are now due for new cards across the board for all staff. We felt this would be a good time to start fresh with a new design. Our traditional card simply had our details on the front, and a list of services on the back. We don't particularly need the list of services, we have had cards where the only thing on the rear of the card was our logo.
Feel free to be creative, we would like our tag line "Complete IT Management" to appear at some point, doesn't necessarily have to be with the logo.
I have attached samples and drafts of various previous cards we have used over the years.

```html
<!DOCTYPE html>
<html lang="en">
<head>
<meta charset="utf-8">
<title>Tidewell Networks – Business Card</title>
<link href="https://fonts.googleapis.com/css2?family=Open+Sans:wght@400;600;700;800&display=swap" rel="stylesheet">
<style>
  :root {
    --backdrop: #e6e4e0;
    --silver-light: #f4f5f6;
    --silver-mid: #dcdfe2;
    --silver-dark: #c7cbcf;
    --slate: #5b6b78;
    --slate-deep: #4a5863;
    --band-grey: #5e6164;
    --text-dark: #3c4248;
    --text-light: #f2f2f2;
  }
  * { box-sizing: border-box; margin: 0; padding: 0; }
  html, body { width: 1200px; height: 720px; overflow: hidden; }
  body {
    background: var(--backdrop);
    font-family: "Open Sans", Arial, sans-serif;
    position: relative;
  }
  .card {
    position: absolute;
    top: 205px;
    width: 540px;
    height: 309px;
    background: linear-gradient(160deg, var(--silver-light) 0%, var(--silver-mid) 55%, var(--silver-dark) 100%);
    box-shadow: 0 3px 10px rgba(0,0,0,0.18);
    overflow: hidden;
  }
  .card--front { left: 40px; }
  .card--back { left: 620px; }

  .card__shapes { position: absolute; inset: 0; }

  .front__brand {
    position: absolute;
    left: 40px;
    top: 112px;
    width: 236px;
    display: flex;
    align-items: center;
    gap: 10px;
  }
  .brand__square {
    width: 44px; height: 44px;
    flex: none;
    background: var(--slate);
  }
  .brand__name {
    font-weight: 800;
    color: var(--slate);
    font-size: 23px;
    line-height: 1.05;
    letter-spacing: 0.5px;
    text-transform: uppercase;
  }

  .contact {
    position: absolute;
    left: 298px;
    top: 14px;
    width: 230px;
    color: var(--text-dark);
  }
  .contact__name { font-weight: 700; font-size: 15px; color: var(--slate-deep); }
  .contact__role { font-size: 11px; margin-bottom: 6px; }
  .contact__list { list-style: none; font-size: 11px; line-height: 15.5px; }
  .contact__list li { display: flex; align-items: center; gap: 6px; white-space: nowrap; }
  .contact__list svg { width: 10px; height: 10px; flex: none; }
  .contact__address { font-size: 11px; line-height: 14px; margin-top: 6px; padding-left: 16px; }

  .tagline {
    position: absolute;
    right: 16px;
    top: 176px;
    color: var(--text-light);
    font-size: 12px;
  }

  .back__brand {
    position: absolute;
    left: 0; right: 0;
    top: 108px;
    display: flex;
    justify-content: center;
    align-items: center;
    gap: 14px;
  }
  .back__brand .brand__square { width: 54px; height: 54px; }
  .back__brand .brand__name { font-size: 38px; }
  .back__web {
    position: absolute;
    left: 0; right: 0;
    bottom: 26px;
    text-align: center;
    font-weight: 600;
    font-size: 15px;
    letter-spacing: 1.5px;
    color: var(--text-dark);
  }
</style>
</head>
<body>

  <section class="card card--front" aria-label="Business card front">
    <svg class="card__shapes" viewBox="0 0 540 309" aria-hidden="true">
      <polygon points="300,172 540,172 540,198 276,198" fill="var(--band-grey)"/>
      <polygon points="0,228 244,228 270,200 290,200 258,244 0,244" fill="var(--slate)"/>
    </svg>

    <div class="front__brand">
      <span class="brand__square"></span>
      <span class="brand__name">Tidewell<br>Networks</span>
    </div>

    <div class="contact">
      <p class="contact__name">Daniel Reeves</p>
      <p class="contact__role">Operation Manager</p>
      <ul class="contact__list">
        <li>
          <svg viewBox="0 0 10 10"><circle cx="5" cy="5" r="5" fill="var(--slate)"/><path d="M3 2.5 L4 2.5 L4.5 4 L3.8 4.6 Q4.5 5.8 5.4 6.2 L6 5.5 L7.5 6 L7.5 7 Q4 7.5 3 2.5Z" fill="#fff"/></svg>
          08 5550 1840
        </li>
        <li>
          <svg viewBox="0 0 10 10"><circle cx="5" cy="5" r="5" fill="var(--slate)"/><rect x="3.6" y="2" width="2.8" height="6" rx="0.5" fill="#fff"/></svg>
          0400 555 017
        </li>
        <li>
          <svg viewBox="0 0 10 10"><circle cx="5" cy="5" r="5" fill="var(--slate)"/><rect x="2.5" y="4" width="5" height="3" fill="#fff"/><rect x="3.5" y="2.4" width="3" height="1.8" fill="#fff"/></svg>
          08 5550 1841
        </li>
        <li>
          <svg viewBox="0 0 10 10"><circle cx="5" cy="5" r="5" fill="var(--slate)"/><rect x="2.4" y="3.2" width="5.2" height="3.6" fill="#fff"/><path d="M2.4 3.2 L5 5.2 L7.6 3.2" stroke="var(--slate)" stroke-width="0.6" fill="none"/></svg>
          daniel@tidewellnetworks.com.au
        </li>
        <li>
          <svg viewBox="0 0 10 10"><circle cx="5" cy="5" r="5" fill="var(--slate)"/><circle cx="5" cy="5" r="2.6" fill="none" stroke="#fff" stroke-width="0.7"/><path d="M2.4 5 H7.6 M5 2.4 V7.6" stroke="#fff" stroke-width="0.6"/></svg>
          www.tidewellnetworks.com.au
        </li>
      </ul>
      <p class="contact__address">Unit 4 12 Marlin Court<br>Harbourvale WA 6100</p>
    </div>

    <p class="tagline">Complete IT Management</p>
  </section>

  <section class="card card--back" aria-label="Business card back">
    <div class="back__brand">
      <span class="brand__square"></span>
      <span class="brand__name">Tidewell</span>
    </div>
    <p class="back__web">www.tidewellnetworks.com.au</p>
  </section>

</body>
</html>
```